Automotive Accessories Business Card

Design a business template that match our new logo design and our industry.

https://www.qelmotorgear.com/

Target Market(s)

Aftermarket auto parts and accessories

Industry/Entity Type

automotive

Contact Information for Business Card

company logo

Font styles to use
Serif
Sans Serif

Colors
EB3D1F
EC4F4E
F09395
F8D3D4
FCEDEE

```html
<!DOCTYPE html>
<html lang="en">
<head>
<meta charset="utf-8">
<title>QEL Motor Gear – Business Card</title>
<link href="https://fonts.googleapis.com/css2?family=Michroma&family=Roboto:wght@300;400;500;700&display=swap" rel="stylesheet">
<style>
  :root {
    --red: #d71f26;
    --charcoal: #363636;
    --charcoal-deep: #262626;
    --ink: #3a3a3a;
    --paper: #ffffff;
    --backdrop: #dcdcdb;
    --photo-tint: #ececec;
  }
  * { margin: 0; padding: 0; box-sizing: border-box; }
  html, body { width: 1200px; height: 800px; overflow: hidden; }
  body {
    background: var(--backdrop);
    font-family: "Roboto", Arial, sans-serif;
    color: var(--ink);
    position: relative;
  }
  .card {
    position: absolute;
    top: 245px;
    width: 540px;
    height: 310px;
    overflow: hidden;
    box-shadow: 0 6px 18px rgba(0,0,0,0.22);
  }
  /* Front */
  .card--front { left: 40px; background: var(--paper); }
  .vehicle-photo {
    position: absolute;
    left: 40px; top: 40px;
    width: 360px; height: 220px;
    background: radial-gradient(ellipse at 55% 50%, #e4e4e4 0%, #f0f0f0 55%, rgba(255,255,255,0) 80%);
  }
  .front-brand {
    position: absolute;
    right: 30px; top: 26px;
    font-family: "Roboto", Arial, sans-serif;
    font-weight: 700;
    font-size: 26px;
    color: var(--red);
    display: flex; align-items: center; gap: 8px;
  }
  .front-brand .brand-dot { width: 12px; height: 12px; background: var(--charcoal); }
  .online {
    position: absolute; right: 30px; top: 92px;
    text-align: right; font-size: 13px; line-height: 20px;
  }
  .online li { list-style: none; display: flex; justify-content: flex-end; align-items: center; gap: 6px; }
  .online svg { width: 11px; height: 11px; }
  .rule {
    position: absolute; left: 30px; right: 30px; top: 150px;
    height: 2px; background: var(--red);
  }
  .person { position: absolute; left: 30px; top: 96px; }
  .person-name {
    font-family: "Michroma", "Arial Black", sans-serif;
    font-size: 22px; color: var(--red); letter-spacing: 0.5px; line-height: 28px;
  }
  .person-title { font-size: 14px; font-weight: 400; line-height: 18px; }
  .office { position: absolute; top: 162px; font-size: 13px; line-height: 17px; }
  .office--us { left: 30px; }
  .office--ca { right: 30px; text-align: right; }
  .office .phone { margin-top: 6px; font-weight: 700; font-size: 14px; }
  .office .phone span { color: var(--red); font-weight: 500; margin-right: 4px; }
  .front-band { position: absolute; left: 0; bottom: 0; width: 540px; height: 60px; }
  /* Back */
  .card--back {
    left: 620px;
    background: radial-gradient(ellipse at 60% 40%, #444 0%, var(--charcoal) 50%, var(--charcoal-deep) 100%);
  }
  .back-brand {
    position: absolute; left: 0; right: 0; top: 110px;
    text-align: center;
    font-family: "Roboto", Arial, sans-serif; font-weight: 700;
    font-size: 40px; color: var(--red);
    display: flex; justify-content: center; align-items: center; gap: 12px;
  }
  .back-brand .brand-dot { width: 16px; height: 16px; background: var(--paper); }
  .web-band { position: absolute; left: 0; bottom: 0; width: 540px; height: 84px; }
  .web-address {
    position: absolute; right: 26px; bottom: 22px;
    color: var(--red); font-size: 15px; letter-spacing: 4px; font-weight: 300;
  }
  .web-address strong { font-weight: 500; }
</style>
</head>
<body>

<section class="card card--front" aria-label="Business card front">
  <div class="vehicle-photo" role="img" aria-label="Faint photo of a white off-road vehicle"></div>

  <div class="front-brand"><span class="brand-dot"></span>QEL Motor Gear</div>

  <ul class="online">
    <li>sales@qelmotorgear.com
      <svg viewBox="0 0 12 12"><rect x="0.5" y="2" width="11" height="8" fill="#d71f26"/><path d="M0.5 2 L6 7 L11.5 2" stroke="#fff" fill="none"/></svg>
    </li>
    <li>qelmotorgear.com
      <svg viewBox="0 0 12 12"><circle cx="6" cy="6" r="5.5" fill="#d71f26"/><path d="M1 6 H11 M6 1 V11" stroke="#fff" stroke-width="0.8"/></svg>
    </li>
  </ul>

  <div class="person">
    <h1 class="person-name">MARCUS HALE</h1>
    <p class="person-title">Founder &amp; CEO</p>
  </div>

  <div class="rule"></div>

  <address class="office office--us" style="font-style:normal">
    240 W. Harbor Ave. Unit C<br>
    Riverton, CA, 92507<br>
    United States
    <p class="phone"><span>T</span>1-866-555-0148</p>
  </address>

  <address class="office office--ca" style="font-style:normal">
    1527 Cedarline Rd<br>
    Burnaby, BC V5G 2K4<br>
    Canada
    <p class="phone"><span>T</span>604-555-0193</p>
  </address>

  <svg class="front-band" viewBox="0 0 540 60" preserveAspectRatio="none" aria-hidden="true">
    <polygon points="0,54 430,36 540,0 540,60 0,60" fill="#d71f26"/>
    <polygon points="430,36 540,0 540,60 500,60" fill="#363636"/>
  </svg>
</section>

<section class="card card--back" aria-label="Business card back">
  <div class="back-brand"><span class="brand-dot"></span>QEL Motor Gear</div>
  <svg class="web-band" viewBox="0 0 540 84" preserveAspectRatio="none" aria-hidden="true">
    <polygon points="270,44 540,0 540,84 240,84" fill="#ffffff"/>
  </svg>
  <p class="web-address">www.<strong>QELMOTORGEAR</strong>.com</p>
</section>

</body>
</html>
```